African homeware retailer needs a web page design

We need a web page design for a new homeware and accessories store based in Johannesburg, South Africa. Our store carries modern African inspired items from designers that support social development and poverty alleviation initiatives. We have a particular preference for outfits that are centred on the empowerment of women.

Our business celebrates the skill, design and product of African craft and the work of designers looking to take that forward in a socially beneficial way (creating employment, developing skills, supporting local crafts people etc). We aim to carry items and inspirations from all over the African continent.

We would like to see a design that communicates African beauty and elegance without the typical tribal references that are made in reference to African craft or art.

We would like the web page to be stylish, uncomplicated, modern, captivating and appealing to the discerning customer. A similar value proposition is that of http://www.marlowtenwick.example/.

This is an e-commerce website which must be attractive to both individual buyers and design professionals so the website needs to look professional.

Here are links to some websites we like:
http://www.quenbyhollis.example/
http://www.dravelo.example/

Our logo is attached to the brief.

Target Market(s)

Our target market is female, age 20-50. However should not alienate the design conscious male customer therefore

Industry/Entity Type

E-Commerce

Requirements
Must have
• - A featured product banner which includes a photograph and text. This should be easy to edit as we will be changing the featured product regularly
- An easily expendable products section with categories. Examples of categories could be cushions, bedding, crockery etc. Should be easy to add new categories as well as new product pictures
- Home/landing page should be uncluttered
- Should use the logo and should be easy to change the logo which we have in various colour combinations. We plan to change the logo colours depending on circumstance e.g. make it red and white around Valentines day (similar to the way Vintrel frequently changes the logo on their landing page)

```html
<!DOCTYPE html>
<html lang="en">
<head>
<meta charset="utf-8">
<title>Amani Nest — homeware &amp; accessories</title>
<link href="https://fonts.googleapis.com/css2?family=Noto+Serif:ital,wght@0,400;0,700;1,400&family=Ubuntu:wght@400;500;700&family=Arimo:ital,wght@0,400;0,700;1,400&display=swap" rel="stylesheet">
<style>
:root{
  --teal:#0f4659;
  --green:#5dbb5e;
  --green-soft:#9bd38f;
  --cream:#fcf8dc;
  --card:#fdf9e4;
  --card-line:#efe3b8;
  --page:#f5f3ea;
  --white:#ffffff;
  --ink:#1d3340;
}
*{box-sizing:border-box;margin:0;padding:0}
html,body{width:1090px;height:1200px;overflow:hidden}
body{background:var(--page);font-family:"Noto Serif",serif;color:var(--ink);position:relative}
.page{position:absolute;left:156px;top:0;width:778px;height:1200px;background:var(--white);box-shadow:0 0 6px rgba(0,0,0,.08)}
.abs{position:absolute}
/* header */
.header{position:absolute;left:156px;top:0;width:778px;height:148px;background:var(--cream)}
.brand{left:166px;top:38px;display:flex;align-items:center;gap:14px}
.brand-mark{width:46px;height:46px;background:var(--green)}
.brand-name{font-family:"Noto Serif",serif;font-weight:700;font-size:34px;color:var(--green);letter-spacing:1px;line-height:1}
.tagline{left:226px;top:92px;font-size:9px;letter-spacing:1px;color:var(--teal)}
.utility{right:170px;top:16px;font-family:"Ubuntu",sans-serif;font-size:10.5px;color:var(--teal);display:flex;gap:8px}
.utility span.sep{color:#bbb}
.callbar{left:604px;top:46px;width:315px;height:33px;background:var(--teal);border:2px solid var(--green);color:#fff;font-weight:700;font-size:14.5px;display:flex;align-items:center;justify-content:center}
.search{left:701px;top:98px;width:215px;height:28px;background:var(--green-soft);font-family:"Ubuntu",sans-serif;font-size:11px;color:var(--teal);display:flex;align-items:center;padding:0 9px;justify-content:space-between}
/* nav */
.nav{left:152px;top:148px;width:786px;height:40px;background:var(--green);display:flex;box-shadow:0 2px 3px rgba(0,0,0,.15)}
.nav a{color:#fff;text-decoration:none;font-weight:700;font-size:10.5px;text-transform:uppercase;display:flex;align-items:center;justify-content:center;border-right:1px solid #4fa650;height:100%}
.nav a.active{background:var(--teal);color:var(--green-soft)}
/* category */
.category{left:172px;top:210px;width:194px}
.cat-head{height:27px;background:var(--teal);color:#fff;font-weight:700;font-size:12px;padding:7px 10px}
.cat-item{height:50px;background:linear-gradient(#fbfbfb,#ececec);border-bottom:1px solid #fff;display:flex;align-items:center;justify-content:space-between;padding:0 14px 0 10px;font-weight:700;font-size:12px;color:var(--teal)}
.cat-thumb{width:42px;height:36px;border-radius:4px}
.cat-all{height:22px;border:1px solid #eee;font-size:10px;font-weight:700;padding:4px 6px;color:#555}
.newsletter{left:172px;top:418px;width:194px;height:62px;border:1px solid #eee;padding:6px 14px}
.newsletter h3{font-size:10.5px;letter-spacing:.5px;color:var(--teal)}
.news-field{margin-top:7px;display:flex;height:29px}
.news-field span{flex:1;border:1px solid #ddd;font-family:"Ubuntu",sans-serif;font-size:10.5px;color:#aaa;padding:7px 10px}
.news-field b{width:29px;background:var(--teal);color:#fff;font-size:18px;font-weight:400;display:flex;align-items:center;justify-content:center}
/* hero */
.hero{left:383px;top:209px;width:534px;height:271px;background:linear-gradient(120deg,#cfe9b6,#e9f5d8 60%,#d3ebbd)}
.hero-art{left:10px;top:10px;width:340px;height:250px;border-radius:8px;background:radial-gradient(circle at 30% 30%,#7d5a3a,#b9a07a 45%,rgba(200,215,170,0) 75%)}
.hero-text{left:205px;top:70px;width:300px;font-weight:700;font-size:24px;line-height:31px;color:var(--teal)}
.dots{right:12px;bottom:6px;display:flex;gap:3px}
.dots i{width:6px;height:6px;background:#fff}
.dots i:first-child{background:var(--teal)}
/* promo */
.promo{top:497px;width:239px;height:67px;border:3px solid;text-align:center;color:#fff}
.promo h2{font-weight:400;font-size:24px;line-height:30px;margin-top:4px}
.promo p{font-family:"Ubuntu",sans-serif;font-size:12px}
.p1{left:171px;background:var(--teal);border-color:var(--teal);box-shadow:inset 0 0 0 2px #fff}
.p2{left:426px;background:var(--green);border-color:var(--green);box-shadow:inset 0 0 0 2px #fff}
.p3{left:680px;background:var(--green-soft);border-color:var(--green-soft);box-shadow:inset 0 0 0 2px #fff}
/* products */
.product{width:179px;height:182px;border:1px solid var(--card-line);background:radial-gradient(circle at 50% 70%,#fff,var(--card) 70%);font-family:"Arimo",sans-serif;color:var(--ink);padding:8px 9px}
.product em{font-size:12px;display:block}
.product strong{font-size:14.5px;line-height:22px;display:block;margin-top:2px}
.product .plain{font-weight:400}
.product h4{font-weight:400;font-size:15px;margin-top:5px}
.prod-img{position:absolute;left:20px;right:20px;bottom:12px;height:80px;border-radius:40%}
.row2 .prod-img{height:120px;bottom:16px;left:35px;right:35px}
.divider{left:171px;top:983px;width:746px;height:2px;background:#eee}
/* footer */
.foot-card{left:171px;top:1005px;width:187px;height:176px;background:var(--green);border:5px solid var(--teal);color:#fff;text-align:center;font-weight:700;font-size:10px;line-height:15px;padding-top:14px}
.foot-mark{width:36px;height:36px;background:var(--teal);margin:0 auto 20px}
.foot-card p+p{margin-top:8px}
.foot-card .mail{font-size:9.5px;letter-spacing:-.2px}
.foot-h{font-family:"Ubuntu",sans-serif;font-weight:700;font-size:12.5px;color:var(--ink)}
.links{font-size:10.5px;line-height:22px;color:var(--teal);list-style:none}
.links li::before{content:"› ";font-weight:700}
.social{left:638px;top:1057px;display:grid;grid-template-columns:repeat(3,30px);gap:4px}
.social i{width:30px;height:30px;display:block}
.pay{font-family:"Ubuntu",sans-serif;font-size:8px;color:var(--teal);font-weight:500}
.pay-row{display:flex;gap:5px;margin-top:9px}
.pay-row span{border:1px solid #ddd;padding:3px 3px}
.pay-big{font-size:13px;font-weight:700;color:var(--teal)}
</style>
</head>
<body>
<div class="page"></div>

<header class="header"></header>
<div class="abs brand"><div class="brand-mark"></div><div class="brand-name">AMANI NEST</div></div>
<div class="abs tagline">homeware &amp; accessories</div>
<div class="abs utility"><span>My Account</span><span class="sep">|</span><span>My Bag (0)</span><span class="sep">|</span><span>Checkout →</span></div>
<div class="abs callbar">Call Us for any Question at: 0198 765 432</div>
<div class="abs search"><span>Search ...</span>
  <svg width="16" height="16" viewBox="0 0 16 16"><circle cx="6.5" cy="6.5" r="5" fill="none" stroke="#0f4659" stroke-width="2"/><line x1="10.2" y1="10.2" x2="15" y2="15" stroke="#0f4659" stroke-width="2"/></svg>
</div>

<nav class="abs nav">
  <a class="active" style="width:84px">Shop Now</a>
  <a style="width:89px">Our Story</a>
  <a style="width:58px">Blog</a>
  <a style="width:114px">Custom Design</a>
  <a style="width:76px">Our Shop</a>
  <a style="width:132px">Press &amp; Mentions</a>
  <a style="width:164px">Designer &amp; Architects</a>
  <a style="width:69px;border-right:0">Contact</a>
</nav>

<aside class="abs category">
  <div class="cat-head">CATEGORY</div>
  <div class="cat-item">Cushions<div class="cat-thumb" role="img" aria-label="Striped cushion" style="background:linear-gradient(#e24b6b,#f2c23a)"></div></div>
  <div class="cat-item">Bedding<div class="cat-thumb" role="img" aria-label="Patterned bedding" style="background:linear-gradient(#6b5442,#2a211b)"></div></div>
  <div class="cat-item">Crockery<div class="cat-thumb" role="img" aria-label="Painted bowl" style="border-radius:50%;background:radial-gradient(#f5b632,#e0451f 60%,#333)"></div></div>
  <div class="cat-all">View All</div>
</aside>
<div class="abs newsletter">
  <h3>JOIN OUR NEWSLETTER</h3>
  <div class="news-field"><span>Enter your email...</span><b>+</b></div>
</div>

<section class="abs hero">
  <div class="abs hero-art" role="img" aria-label="Featured product: a beaded wall mask with woven chairs and a carved figure"></div>
  <div class="abs hero-text">Ut wisi enim ad minim veniam, quis nostrud exerci tation</div>
  <div class="abs dots"><i></i><i></i><i></i><i></i><i></i></div>
</section>

<div class="abs promo p1"><h2>What's New</h2><p>Check our latest collections out!</p></div>
<div class="abs promo p2"><h2>Best Selling Product</h2><p>Shop our best sale collections!</p></div>
<div class="abs promo p3"><h2>Partner With Us</h2><p>Lorem ipsum dolor consectet</p></div>

<div class="abs product" style="left:171px;top:586px"><em>Lorem ipsum dolor</em><strong>Sit amet, consectetu adipiscing</strong>
  <div class="prod-img" role="img" aria-label="Carved wooden bowl" style="background:linear-gradient(#c56a35,#8a3f1c)"></div></div>
<div class="abs product" style="left:360px;top:586px"><em>Lorem ipsum dolor</em><strong class="plain">Sit amet, consectetu adipiscing</strong>
  <div class="prod-img" role="img" aria-label="Woven baskets" style="background:linear-gradient(90deg,#3a8f7c,#e5a548)"></div></div>
<div class="abs product" style="left:549px;top:586px"><em>Lorem ipsum dolor</em><strong class="plain">Sit amet, consectetu adipiscing</strong>
  <div class="prod-img" role="img" aria-label="Pile of printed cushions" style="background:linear-gradient(90deg,#c9202b,#25357a,#f2c23a)"></div></div>
<div class="abs product" style="left:738px;top:586px"><em>Lorem ipsum dolor</em><strong class="plain">Sit amet, consectetu adipiscing</strong>
  <div class="prod-img" role="img" aria-label="White porcelain tea set" style="background:linear-gradient(#f4f2ea,#d7cfb5)"></div></div>

<div class="abs product row2" style="left:171px;top:783px"><h4>Lorem Ispum Lorem</h4>
  <div class="prod-img" role="img" aria-label="Striped woven basket bag" style="background:linear-gradient(#d9b26a,#1f4f6b,#d9b26a)"></div></div>
<div class="abs product row2" style="left:360px;top:783px"><h4>Lorem Ispum Lorem</h4>
  <div class="prod-img" role="img" aria-label="Beaded wire animal figure" style="background:linear-gradient(#e6e6e6,#555)"></div></div>
<div class="abs product row2" style="left:549px;top:783px"><h4>Lorem Ispum Lorem</h4>
  <div class="prod-img" role="img" aria-label="Patterned ceramic vase" style="background:linear-gradient(#b7772f,#2d3a42)"></div></div>
<div class="abs product row2" style="left:738px;top:783px"><h4>Lorem Ispum Lorem</h4>
  <div class="prod-img" role="img" aria-label="Wooden salad servers" style="background:linear-gradient(90deg,#ddd,#b35a1a)"></div></div>

<div class="abs divider"></div>

<footer>
  <div class="abs foot-card">
    <div class="foot-mark"></div>
    <p>Copyright © 2014. Amaninest<br>All Rights Reserved.</p>
    <p><span class="mail">Email: info@amaninest.example</span><br>Phone: 0198 765 432<br>Fax: 0198 765 432</p>
  </div>
  <div class="abs foot-h" style="left:385px;top:1024px">More Info</div>
  <ul class="abs links" style="left:386px;top:1050px">
    <li>Shop Now</li><li>Our Story</li><li>Blog</li><li>Custom Design</li><li>Our Shop</li>
  </ul>
  <ul class="abs links" style="left:484px;top:1050px">
    <li>Press &amp; Mentions</li><li>Designer &amp; Architects</li><li>Contact</li>
  </ul>
  <div class="abs foot-h" style="left:637px;top:1024px">Keep in Touch</div>
  <div class="abs social" aria-label="Social links">
    <i style="background:#3b5a9a"></i><i style="background:#2fa9e0"></i><i style="background:#dd4b39"></i>
    <i style="background:#d4231f"></i><i style="background:#cb2027"></i><i style="background:#f26b21"></i>
  </div>
  <div class="abs foot-h" style="left:772px;top:1024px">Payment Methods</div>
  <div class="abs pay" style="left:772px;top:1048px;width:145px">
    <div class="pay-row"><span>Velta</span><span>Orbica</span><span>Azurepay</span><span>Findly</span></div>
    <div class="pay-row" style="margin-top:12px;gap:14px"><span class="pay-big" style="border:0;padding:0">Passpurse</span><span class="pay-big" style="border:0;padding:0">BankDraw</span></div>
  </div>
</footer>
</body>
</html>
```